Church Website with Home Page and Member Sermon Library

I am in need of an updated design for our church website. This will include 4 pages (outlined below). We are a conservative, evangelical, Christian church. The site should be modern and clean, while still reflecting our conservative values. I already have a logo for our church, and I want the site to incorporate the logo, and match the logo/branding. Stock photos are allowed if needed, but I have uploaded some images of our church and would prefer those images to be used if possible. Any stock photos used should not include any people in the photos (scenery, nature, buildings, animals, etc. are fine).

The site will need 4 pages: Home, Support Us (Donate), Login, and Recording Library.

Page 1: Home
The home page should include the following sections:

- Navigation: Should include links to each section of the home page plus a "listen live" link which will take the user to a live-streaming site and a "support us" link which will take the user to a support/donate page.

- Announcements: Can be either a banner or some other design, but there needs to be some way for us to post announcements for visitors to see. I'm open for creative ideas in this section, but would like it not to take up a lot of room on the page.

- About Us: Should include address, service times (see attached document), and information about the church.

- Pastor Bio: A section that introduces our pastor and gives a short bio about our pastor. Would like this section to include a picture of our pastor. Somewhere in this section I would like to include this Bible reference: "And I will give you pastors according to mine heart, which shall feed you with knowledge and understanding. Jer 3:15 LPW"

- Articles of Faith (What We Believe): This should include several sub-sections each with a heading, body, and possibly 1 or more scripture references. I have attached a document to the brief that includes our articles of faith. Feel free to be creative with this section in how you lay these out and format them.

- Support Us: A small section that explains what kind of support someone can give and a link to a donation page. The link can say something like "Support Us" or "Donate Now".

- Contact form: A contact form that allows the visitor to send us a message. The contact form should ask for name, email, phone, and message.

- Footer: A footer that will be displayed on all pages of the site. This should include at a minimum a link to the home page (or a link to each individual section in the home page if you prefer), a link to "listen live", a link to "support us", a link to "contact us" (or you can put the contact form directly in the footer if you prefer), the address, and a "member login" link.

Page 2: Support Us
The donation page should include a form the visitor can fill out to make a donation. We will embed a third party form later. For this design, please just mock out the design with a basic form asking for name, phone, and email.

Page 3: Login
The recording library (detailed below) will require members to login with a shared numeric code before accessing the page. We need a design for a login screen. The screen should include navigation/footer just like all other pages, but the body of the login page will consist only of a form that asks the user to enter the access code and then a "login" button.

Page 4: Recording Library

The library page is a member-only page that will require a shared, numeric pass code to access. On this page, members will be able to access a filterable list of past sermons. The page by default should display most recent sermons, but should also include a search form that allows the member to filter the sermon list to find a particular sermon. The search form should allow the user to select a filter type (e.g. Speaker name, date, event, etc.) and type in a value to search. They should be able to add multiple filters and remove filters that have been added. Each sermon that is displayed in the result list should include basic information such as title, date, speaker, tags, etc. along with a download icon, and an embedded audio player where they can click a play button to stream it on-demand. Each sermon should also have clickable tags associated with it that can be used to find related sermons.
Updates

I have uploaded several images of our church. Feel free to incorporate these into your design if possible.

Target Market(s)

Church Members

Industry/Entity Type

Religion

Number of Pages Required

4 page

Font styles to use
Sans Serif

Colors

Designer to choose colors to be used in the design.

Requirements
Must have
• Must incorporate the logo (attached)
Nice to have
• Would like the design to incorporate pictures of our church (attached) instead of stock photos if possible.
Should not have
• Please avoid an overly cluttered design. Stock photos used should not include any people in the photos.

```html
<!DOCTYPE html>
<html lang="en">
<head>
<meta charset="utf-8">
<title>Library – Grace Harbor Chapel</title>
<link href="https://fonts.googleapis.com/css2?family=Cinzel:wght@400;500&family=Montserrat:wght@400;500&display=swap" rel="stylesheet">
<style>
:root{
  --green:#80a86a;
  --green-dark:#2f4d26;
  --ink:#1c1c1c;
  --muted:#555;
  --rule:#dcdcdc;
  --footer:#2b2b2b;
  --footer-line:#8a8a8a;
  --white:#fff;
}
*{box-sizing:border-box;margin:0;padding:0}
html,body{width:686px;height:1200px;overflow:hidden;background:var(--white)}
body{position:relative;font-family:"Montserrat",sans-serif;color:var(--ink)}
.abs{position:absolute}
.serif{font-family:"Cinzel",serif}

/* hero */
.hero{left:0;top:0;width:686px;height:260px;
  background:linear-gradient(180deg,#fbf8f5 0%,#f1dfd0 30%,#d9a47a 60%,#b97a4f 85%,#8a6a58 100%)}
.hero-fade{left:0;top:0;width:686px;height:260px;
  background:radial-gradient(ellipse at 50% 55%,rgba(255,255,255,.75),rgba(255,255,255,0) 60%)}
.brand{left:80px;top:28px;width:82px;text-align:center;color:var(--green);font-family:"Cinzel",serif;font-size:11px;line-height:13px;letter-spacing:1px}
.brand-dot{display:block;margin:0 auto 5px;width:14px;height:14px;border-radius:50%;background:var(--green)}
.nav{top:29px;left:301px;display:flex;gap:0;font-size:7.8px;color:var(--ink)}
.nav a{color:inherit;text-decoration:none;position:absolute;white-space:nowrap}
.btn-donate{background:var(--green);color:var(--white);font-family:"Cinzel",serif;font-size:8.5px;display:flex;align-items:center;justify-content:center}
.page-title{left:0;width:686px;top:137px;text-align:center;font-size:33px;letter-spacing:3px;color:var(--ink)}
.title-rule{height:1.5px;background:var(--ink)}

/* sermons */
.section-head{font-size:13px;letter-spacing:1.3px;color:var(--ink)}
.hr{height:1px;background:var(--rule)}
.search{left:99px;top:326px;width:368px;height:30px;border:1px solid var(--rule);border-right:none}
.search svg{position:absolute;left:10px;top:10px}
.speaker{left:467px;top:326px;width:120px;height:30px;background:var(--green);color:var(--white);font-size:8.5px;font-weight:500;display:flex;align-items:center;padding-left:11px}
.speaker svg{position:absolute;right:11px;top:13px}

.card{width:237px;height:148px;overflow:hidden;color:var(--white)}
.card-photo{position:absolute;inset:0;background:linear-gradient(180deg,#5f7f55 0%,#b8c6ae 25%,#809a74 50%,#3d6231 78%,#2f5326 100%)}
.card-photo.alt{background:linear-gradient(180deg,#4f7046 0%,#d2dccb 28%,#8da57f 52%,#3f6634 78%,#2e5225 100%)}
.dl{position:absolute;left:11px;top:11px;font-size:7px;display:flex;align-items:center;gap:5px;color:#f0f0f0}
.date{position:absolute;left:11px;top:67px;font-size:6.5px;display:flex;gap:3px;align-items:center;color:#eee}
.card-title{position:absolute;left:10px;top:76px;font-size:8px;letter-spacing:.8px;font-weight:500}
.desc{position:absolute;left:11px;top:89px;width:165px;font-size:5.2px;line-height:6.7px;color:#eee}
.by{position:absolute;left:11px;top:117px;font-size:7px;display:flex;align-items:center;gap:5px}
.avatar{width:13px;height:13px;border-radius:50%;background:#c9b7a6;border:1px solid #fff}
.tags{position:absolute;left:11px;top:131px;font-size:6.8px;display:flex;align-items:center;gap:2px}
.chip{border:1px solid var(--white);border-radius:6px;padding:1px 5px;letter-spacing:.5px}
.play{position:absolute;left:185px;top:69px;width:40px;height:40px;border-radius:50%;background:rgba(200,205,200,.7);border:1.5px solid #9cc78b}
.play svg{position:absolute;left:15px;top:13px}

.related{display:flex;flex-wrap:wrap;gap:6px;left:100px;top:895px;width:490px}
.rtag{height:19px;border:1px solid var(--rule);border-radius:10px;padding:0 9px;font-size:8px;letter-spacing:1px;color:var(--muted);display:flex;align-items:center}

/* footer */
.footer{left:0;top:963px;width:686px;height:237px;background:var(--footer);color:#ddd}
.footer-brand{left:110px;top:1030px;width:124px;text-align:center;color:var(--green);font-family:"Cinzel",serif;font-size:17px;line-height:20px;letter-spacing:1.5px}
.footer-brand .brand-dot{width:22px;height:22px;margin-bottom:8px}
.contact-head{left:272px;top:995px;font-size:11px;letter-spacing:1.5px;color:#eee}
.field{font-size:6.5px;color:#ddd;border-bottom:1px solid var(--footer-line);padding-bottom:3px;display:flex;justify-content:space-between;align-items:center}
.send{left:272px;top:1104px;width:63px;height:20px;border:1px solid var(--green);color:var(--green);font-family:"Cinzel",serif;font-size:8px;display:flex;align-items:center;justify-content:center;gap:4px}
.note{left:272px;top:1145px;font-size:6.8px;color:#ddd}
.foot-rule{left:0;top:1170px;width:686px;height:1px;background:#3a3a3a}
.copy{left:106px;top:1183px;font-size:6.8px;color:#ddd}
.social{left:530px;top:1184px;display:flex;gap:10px}
.social span{width:6px;height:6px;border-radius:50%;background:var(--white);display:block}
</style>
</head>
<body>

<div class="abs hero" role="img" aria-label="Photo of wooden church pews"></div>
<div class="abs hero-fade"></div>

<div class="abs brand"><span class="brand-dot"></span>Grace Harbor<br><span style="font-size:7px;letter-spacing:2px">Chapel</span></div>

<nav class="abs nav">
  <a href="#" style="left:0">Home</a>
  <a href="#" style="left:43px">About</a>
  <a href="#" style="left:87px">Our Pastor</a>
  <a href="#" style="left:148px">Articles Of Faith</a>
</nav>
<div class="abs btn-donate" style="left:531px;top:24px;width:57px;height:21px">DONATE</div>

<h1 class="abs page-title serif" style="font-weight:400">LIBRARY</h1>
<div class="abs title-rule" style="left:296px;top:181px;width:93px"></div>
<div class="abs title-rule" style="left:320px;top:185px;width:45px;height:.7px"></div>

<h2 class="abs section-head serif" style="left:99px;top:290px;font-weight:400">LIST OF PAST SERMONS</h2>
<div class="abs hr" style="left:99px;top:310px;width:488px"></div>

<div class="abs search">
  <svg width="9" height="9" viewBox="0 0 10 10"><circle cx="4" cy="4" r="3" fill="none" stroke="#aaa" stroke-width="1.2"/><line x1="6.2" y1="6.2" x2="9" y2="9" stroke="#aaa" stroke-width="1.4"/></svg>
</div>
<div class="abs speaker">Search by speaker:
  <svg width="6" height="4" viewBox="0 0 6 4"><path d="M0 0h6L3 4z" fill="#fff"/></svg>
</div>

<!-- sermon cards -->
<div class="abs card" style="left:99px;top:370px">
  <div class="card-photo" role="img" aria-label="Sermon photo of a preacher reading scripture"></div>
  <div class="dl"><svg width="7" height="7" viewBox="0 0 8 8"><path d="M4 0v5M2 3l2 2 2-2M0 6v2h8V6" fill="none" stroke="#9cc78b" stroke-width="1"/></svg>Download</div>
  <div class="date"><svg width="6" height="6" viewBox="0 0 6 6"><rect x=".5" y="1" width="5" height="4.5" fill="none" stroke="#eee" stroke-width=".7"/></svg>Fab 12, 2023</div>
  <div class="card-title serif">ULLAMCORPER FACILISI EGESTAS</div>
  <div class="desc">Ut diam tortor consectetur lacus scelerisque tortor congue viverra egestas. Tristique in consectetur leo arcu blandit diam et sed volutpat.</div>
  <div class="play"><svg width="12" height="13" viewBox="0 0 12 13"><path d="M0 0l12 6.5L0 13z" fill="#fff"/></svg></div>
  <div class="by"><span class="avatar"></span>by:&nbsp; Daniel Reeves</div>
  <div class="tags">search tags: <span class="chip">Ullamcorper facilis</span><span class="chip">facilis</span><span class="chip">Ullamcorper</span></div>
</div>

<div class="abs card" style="left:350px;top:370px">
  <div class="card-photo alt" role="img" aria-label="Sermon photo of a speaker holding a Bible"></div>
  <div class="dl"><svg width="7" height="7" viewBox="0 0 8 8"><path d="M4 0v5M2 3l2 2 2-2M0 6v2h8V6" fill="none" stroke="#9cc78b" stroke-width="1"/></svg>Download</div>
  <div class="date"><svg width="6" height="6" viewBox="0 0 6 6"><rect x=".5" y="1" width="5" height="4.5" fill="none" stroke="#eee" stroke-width=".7"/></svg>Fab 12, 2023</div>
  <div class="card-title serif">ULLAMCORPER FACILISI EGESTAS</div>
  <div class="desc">Ut diam tortor consectetur lacus scelerisque tortor congue viverra egestas. Tristique in consectetur leo arcu blandit diam et sed volutpat.</div>
  <div class="play"><svg width="12" height="13" viewBox="0 0 12 13"><path d="M0 0l12 6.5L0 13z" fill="#fff"/></svg></div>
  <div class="by"><span class="avatar"></span>by:&nbsp; Daniel Reeves</div>
  <div class="tags">search tags: <span class="chip">Ullamcorper facilis</span><span class="chip">facilis</span><span class="chip">Ullamcorper</span></div>
</div>

<div class="abs card" style="left:99px;top:531px">
  <div class="card-photo alt" role="img" aria-label="Sermon photo of a speaker holding a Bible"></div>
  <div class="dl"><svg width="7" height="7" viewBox="0 0 8 8"><path d="M4 0v5M2 3l2 2 2-2M0 6v2h8V6" fill="none" stroke="#9cc78b" stroke-width="1"/></svg>Download</div>
  <div class="date"><svg width="6" height="6" viewBox="0 0 6 6"><rect x=".5" y="1" width="5" height="4.5" fill="none" stroke="#eee" stroke-width=".7"/></svg>Fab 12, 2023</div>
  <div class="card-title serif">ULLAMCORPER FACILISI EGESTAS</div>
  <div class="desc">Ut diam tortor consectetur lacus scelerisque tortor congue viverra egestas. Tristique in consectetur leo arcu blandit diam et sed volutpat.</div>
  <div class="play"><svg width="12" height="13" viewBox="0 0 12 13"><path d="M0 0l12 6.5L0 13z" fill="#fff"/></svg></div>
  <div class="by"><span class="avatar"></span>by:&nbsp; Daniel Reeves</div>
  <div class="tags">search tags: <span class="chip">Ullamcorper facilis</span><span class="chip">facilis</span><span class="chip">Ullamcorper</span></div>
</div>

<div class="abs card" style="left:350px;top:531px">
  <div class="card-photo" role="img" aria-label="Sermon photo of a preacher reading scripture"></div>
  <div class="dl"><svg width="7" height="7" viewBox="0 0 8 8"><path d="M4 0v5M2 3l2 2 2-2M0 6v2h8V6" fill="none" stroke="#9cc78b" stroke-width="1"/></svg>Download</div>
  <div class="date"><svg width="6" height="6" viewBox="0 0 6 6"><rect x=".5" y="1" width="5" height="4.5" fill="none" stroke="#eee" stroke-width=".7"/></svg>Fab 12, 2023</div>
  <div class="card-title serif">ULLAMCORPER FACILISI EGESTAS</div>
  <div class="desc">Ut diam tortor consectetur lacus scelerisque tortor congue viverra egestas. Tristique in consectetur leo arcu blandit diam et sed volutpat.</div>
  <div class="play"><svg width="12" height="13" viewBox="0 0 12 13"><path d="M0 0l12 6.5L0 13z" fill="#fff"/></svg></div>
  <div class="by"><span class="avatar"></span>by:&nbsp; Daniel Reeves</div>
  <div class="tags">search tags: <span class="chip">Ullamcorper facilis</span><span class="chip">facilis</span><span class="chip">Ullamcorper</span></div>
</div>

<div class="abs card" style="left:99px;top:692px">
  <div class="card-photo" role="img" aria-label="Sermon photo of a preacher reading scripture"></div>
  <div class="dl"><svg width="7" height="7" viewBox="0 0 8 8"><path d="M4 0v5M2 3l2 2 2-2M0 6v2h8V6" fill="none" stroke="#9cc78b" stroke-width="1"/></svg>Download</div>
  <div class="date"><svg width="6" height="6" viewBox="0 0 6 6"><rect x=".5" y="1" width="5" height="4.5" fill="none" stroke="#eee" stroke-width=".7"/></svg>Fab 12, 2023</div>
  <div class="card-title serif">ULLAMCORPER FACILISI EGESTAS</div>
  <div class="desc">Ut diam tortor consectetur lacus scelerisque tortor congue viverra egestas. Tristique in consectetur leo arcu blandit diam et sed volutpat.</div>
  <div class="play"><svg width="12" height="13" viewBox="0 0 12 13"><path d="M0 0l12 6.5L0 13z" fill="#fff"/></svg></div>
  <div class="by"><span class="avatar"></span>by:&nbsp; Daniel Reeves</div>
  <div class="tags">search tags: <span class="chip">Ullamcorper facilis</span><span class="chip">facilis</span><span class="chip">Ullamcorper</span></div>
</div>

<div class="abs card" style="left:350px;top:692px">
  <div class="card-photo alt" role="img" aria-label="Sermon photo of a speaker holding a Bible"></div>
  <div class="dl"><svg width="7" height="7" viewBox="0 0 8 8"><path d="M4 0v5M2 3l2 2 2-2M0 6v2h8V6" fill="none" stroke="#9cc78b" stroke-width="1"/></svg>Download</div>
  <div class="date"><svg width="6" height="6" viewBox="0 0 6 6"><rect x=".5" y="1" width="5" height="4.5" fill="none" stroke="#eee" stroke-width=".7"/></svg>Fab 12, 2023</div>
  <div class="card-title serif">ULLAMCORPER FACILISI EGESTAS</div>
  <div class="desc">Ut diam tortor consectetur lacus scelerisque tortor congue viverra egestas. Tristique in consectetur leo arcu blandit diam et sed volutpat.</div>
  <div class="play"><svg width="12" height="13" viewBox="0 0 12 13"><path d="M0 0l12 6.5L0 13z" fill="#fff"/></svg></div>
  <div class="by"><span class="avatar"></span>by:&nbsp; Daniel Reeves</div>
  <div class="tags">search tags: <span class="chip">Ullamcorper facilis</span><span class="chip">facilis</span><span class="chip">Ullamcorper</span></div>
</div>

<div class="abs hr" style="left:99px;top:854px;width:488px"></div>
<h2 class="abs section-head serif" style="left:100px;top:869px;font-size:10.5px;font-weight:400">RELATED SERMONS TAGS</h2>
<div class="abs related">
  <span class="rtag">Ullamcorper facilis</span><span class="rtag">eu id tempo</span><span class="rtag">in consectetur leo</span><span class="rtag">elementum gravida</span><span class="rtag">entum gravida</span>
  <span class="rtag">in consectetur leo</span><span class="rtag">elementum gravida</span><span class="rtag">entum gravida</span>
</div>

<!-- footer -->
<footer class="abs footer"></footer>
<div class="abs footer-brand"><span class="brand-dot"></span>Grace Harbor<br><span style="font-size:11px;letter-spacing:3px">Chapel</span></div>

<h2 class="abs contact-head serif" style="font-weight:400">CONTACT US</h2>
<div class="abs field" style="left:272px;top:1029px;width:145px">Full Name:
  <svg width="6" height="6" viewBox="0 0 6 6"><circle cx="3" cy="2" r="1.4" fill="none" stroke="#ddd" stroke-width=".6"/><path d="M.8 6c0-1.5 1-2.3 2.2-2.3S5.2 4.5 5.2 6" fill="none" stroke="#ddd" stroke-width=".6"/></svg></div>
<div class="abs field" style="left:272px;top:1054px;width:145px">Phone:
  <svg width="6" height="6" viewBox="0 0 6 6"><path d="M1 .5l1.3 1.3-.7.8c.5 1 1.1 1.6 2 2l.8-.7L5.6 5.2 4.8 6C2.5 5.6.4 3.5 0 1.2z" fill="none" stroke="#ddd" stroke-width=".6"/></svg></div>
<div class="abs field" style="left:272px;top:1079px;width:145px">Email Address:
  <svg width="7" height="5" viewBox="0 0 7 5"><rect x=".3" y=".3" width="6.4" height="4.4" fill="none" stroke="#ddd" stroke-width=".6"/><path d="M.3.3l3.2 2.4L6.7.3" fill="none" stroke="#ddd" stroke-width=".6"/></svg></div>
<div class="abs field" style="left:433px;top:1029px;width:154px;height:62px;align-items:flex-start">Message
  <svg width="7" height="7" viewBox="0 0 7 7"><path d="M1 6l.3-1.5L5 .8 6.2 2 2.5 5.7z" fill="none" stroke="#ddd" stroke-width=".6"/></svg></div>
<div class="abs send">SEND US <svg width="11" height="4" viewBox="0 0 11 4"><path d="M0 2h10M8 .3L10 2 8 3.7" fill="none" stroke="#80a86a" stroke-width=".7"/></svg></div>

<p class="abs note">Aliquam at commodo venenatis quis. Velit neque interdum molestie risus.</p>
<div class="abs btn-donate" style="left:529px;top:1138px;width:57px;height:21px">DONATE</div>

<div class="abs foot-rule"></div>
<p class="abs copy">Copyright 2023 Grace Harbor Chapel I All rights reserved</p>
<div class="abs social" aria-label="Social links"><span></span><span></span><span></span><span></span></div>

</body>
</html>
```